VOR Exterior Coatings

double sided. the front i want the name of the business each word on a new line with the VOR being bigger. id like teal, black and white colors. the back i want my contact info. Flat, no gloss. Something professional and I want to feel the letters bump put of the card. if possible maybe a paint sprayer in corner. not a car paint spray. (no tank on top of gun)
no vehicle paint sprayers. that means no tank on top of the gun. doesn't have to have a sprayer. black/dark background on the front. white back ground on back with info

```html
<!DOCTYPE html>
<html lang="en">
<head>
<meta charset="utf-8">
<title>VOR Exterior Coatings – Business Card</title>
<link rel="stylesheet" href="https://fonts.googleapis.com/css2?family=Krona+One&family=Roboto:wght@400&display=swap">
<style>
  :root {
    --backdrop: #6e6e6e;
    --teal: #06827f;
    --ink: #262a2b;
    --card-black: #1b1a1b;
    --white: #ffffff;
  }
  html, body {
    margin: 0;
    padding: 0;
    width: 1200px;
    height: 801px;
    overflow: hidden;
    background: var(--backdrop);
  }
  .card {
    position: absolute;
    top: 274px;
    width: 443px;
    height: 263px;
    overflow: hidden;
  }
  .card--info { left: 153px; background: var(--white); }
  .card--brand { left: 625px; background: var(--card-black); }

  .wordmark { position: absolute; display: block; }
  .wordmark text {
    font-family: "Krona One", sans-serif;
    font-weight: 400;
  }
  .card--info .wordmark { left: 236px; top: 33px; }
  .card--info .wordmark text { fill: var(--teal); }
  .card--brand .wordmark { left: 108px; top: 71px; }
  .card--brand .wordmark text { fill: var(--white); }

  .name-tab {
    position: absolute;
    left: 0;
    top: 120px;
    width: 216px;
    height: 55px;
    background: var(--ink);
    clip-path: polygon(0 0, 201px 0, 216px 100%, 0 100%);
  }
  .name-tab__name {
    position: absolute;
    left: 28px;
    top: 12px;
    margin: 0;
    font-family: "Krona One", sans-serif;
    font-size: 14px;
    color: var(--white);
    letter-spacing: 0.3px;
  }
  .name-tab__role {
    position: absolute;
    left: 28px;
    top: 31px;
    margin: 0;
    font-family: "Roboto", sans-serif;
    font-size: 12.5px;
    color: var(--white);
  }

  .contact-band {
    position: absolute;
    left: 0;
    top: 175px;
    width: 443px;
    height: 88px;
    background: var(--teal);
    font-family: "Roboto", sans-serif;
    font-size: 12.5px;
    color: var(--white);
  }
  .contact-list {
    position: absolute;
    left: 28px;
    top: 22px;
    margin: 0;
    padding: 0;
    list-style: none;
  }
  .contact-list li {
    display: flex;
    align-items: center;
    height: 16.5px;
  }
  .contact-list svg { width: 13px; height: 13px; margin-right: 4px; }
  .address {
    position: absolute;
    left: 281px;
    top: 38px;
    margin: 0;
    font-style: normal;
    line-height: 16px;
  }
</style>
</head>
<body>

<section class="card card--info" aria-label="Card back with contact details">
  <svg class="wordmark" width="174" height="96" viewBox="0 0 174 96" aria-label="VOR Exterior Coatings">
    <text x="0" y="44" font-size="48" textLength="172" lengthAdjust="spacingAndGlyphs">VOR</text>
    <text x="2" y="70" font-size="19" textLength="168" lengthAdjust="spacingAndGlyphs">EXTERIOR</text>
    <text x="2" y="91" font-size="19" textLength="166" lengthAdjust="spacingAndGlyphs">COATINGS</text>
  </svg>

  <div class="name-tab">
    <h1 class="name-tab__name">DANIEL REYES</h1>
    <p class="name-tab__role">Managing Director</p>
  </div>

  <div class="contact-band">
    <ul class="contact-list">
      <li>
        <svg viewBox="0 0 16 16" aria-hidden="true"><path d="M4 1.5l2.2 3-1.4 1.6c.8 1.8 2.3 3.3 4.1 4.1l1.6-1.4 3 2.2-1.3 2.6C7 13.4 2.6 9 2.4 2.8z" fill="none" stroke="#fff" stroke-width="1.4" stroke-linejoin="round"/></svg>
        044-123 456 789
      </li>
      <li>
        <svg viewBox="0 0 16 16" aria-hidden="true"><rect x="1" y="3" width="14" height="10" fill="#fff"/><path d="M1 3l7 6 7-6M1 13l5-5M15 13l-5-5" fill="none" stroke="#06827f" stroke-width="1.2"/></svg>
        info@webname.com
      </li>
      <li>
        <svg viewBox="0 0 16 16" aria-hidden="true"><g fill="none" stroke="#fff" stroke-width="1.2"><circle cx="8" cy="8" r="6.8"/><ellipse cx="8" cy="8" rx="3" ry="6.8"/><path d="M1.2 8h13.6M2.5 4.5h11M2.5 11.5h11"/></g></svg>
        www.websitename.com
      </li>
    </ul>
    <address class="address">421, Address line here<br>Country Name, 45452</address>
  </div>
</section>

<section class="card card--brand" aria-label="Card front with business name">
  <svg class="wordmark" width="228" height="122" viewBox="0 0 228 122" aria-label="VOR Exterior Coatings">
    <text x="0" y="56" font-size="62" textLength="226" lengthAdjust="spacingAndGlyphs">VOR</text>
    <text x="3" y="91" font-size="27" textLength="221" lengthAdjust="spacingAndGlyphs">EXTERIOR</text>
    <text x="2" y="119" font-size="26" textLength="219" lengthAdjust="spacingAndGlyphs">COATINGS</text>
  </svg>
</section>

</body>
</html>
```